American cannabis tech company business card design

Pavrel.com is seeking a modern, professional, and brand-aligned business card that represents our company and its core values: Mission, Story, Values, and Impact. As an innovative cannabis company, we want a business card that is not only visually appealing but also serves as a representation of who we are and what we stand for.

Project Scope: Design a double-sided business card that integrates our brand identity and core values. Incorporate our key brand elements, ensuring a sleek and contemporary aesthetic. Visually reflect our core values (Mission, Story, Values, Impact) in a way that is engaging yet professional.

Target Market(s)

Vendors, third parties,

Contact Information for Business Card

Contact details (name, title, email, phone, website, etc.)

Font styles to use
Other font styles liked:
• Caslon, Centra

Colors

Designer to choose colors to be used in the design.

Requirements
Must have
• Pavrel.com logo and branding A creative yet clean way to integrate our core values (Mission, Story, Values, Impact) Modern typography and a well-structured layout
Nice to have
• forest green, grey, white, black
Should not have
• references to marijuana, leafs, plants, or related product

```html
<!DOCTYPE html>
<html lang="en">
<head>
<meta charset="utf-8">
<title>Pavrel.com Business Card</title>
<link href="https://fonts.googleapis.com/css2?family=Poppins:wght@400;600;800&display=swap" rel="stylesheet">
<style>
  :root {
    --forest: #16311a;
    --paper: #ffffff;
    --ink: #222222;
    --stage: #9b9b9b;
    --silver: #d6d6d6;
  }
  * { margin: 0; padding: 0; box-sizing: border-box; }
  html, body {
    width: 1093px; height: 1200px; overflow: hidden;
    background: var(--stage);
    font-family: "Poppins", sans-serif;
  }
  .card {
    position: absolute;
    left: 264px;
    width: 580px;
    height: 356px;
    border-radius: 26px;
    overflow: hidden;
  }
  .card--front { top: 226px; background: var(--paper); }
  .card--back { top: 621px; background: var(--forest); }

  .name-marker {
    position: absolute; left: 0; top: 42px;
    width: 19px; height: 35px; background: var(--forest);
  }
  .identity { position: absolute; left: 29px; top: 38px; }
  .identity__name {
    font-weight: 600; font-size: 23px; line-height: 26px;
    color: var(--forest); letter-spacing: -0.2px;
  }
  .identity__title {
    font-weight: 400; font-size: 17px; line-height: 20px;
    color: var(--ink); letter-spacing: 0.2px;
  }
  .brand-name {
    position: absolute; right: 34px; top: 34px;
    font-weight: 800; font-size: 46px; line-height: 62px;
    color: var(--forest); letter-spacing: -1px;
  }
  .contact { position: absolute; left: 26px; top: 265px; list-style: none; }
  .contact__item {
    display: flex; align-items: center; gap: 5px;
    height: 26px; margin-bottom: 1px;
    font-size: 17.5px; color: var(--ink);
  }
  .contact__icon { width: 25px; height: 25px; flex: none; }
  .website {
    position: absolute; right: 33px; top: 292px;
    font-size: 17.5px; line-height: 26px; color: var(--ink);
  }
  .front-band {
    position: absolute; left: 0; right: 0; bottom: 0;
    height: 12px; background: var(--forest);
  }
  .back-brand {
    position: absolute; left: 0; right: 0; top: 134px;
    text-align: center;
    font-weight: 800; font-size: 76px; line-height: 90px;
    color: var(--silver); letter-spacing: -1.5px;
  }
</style>
</head>
<body>

<section class="card card--front" aria-label="Business card front">
  <div class="name-marker"></div>
  <div class="identity">
    <p class="identity__name">DANIEL HARLOW</p>
    <p class="identity__title">Managing Director</p>
  </div>
  <p class="brand-name">PAVREL</p>

  <ul class="contact">
    <li class="contact__item">
      <svg class="contact__icon" viewBox="0 0 24 24" aria-hidden="true">
        <circle cx="12" cy="12" r="12" fill="var(--forest)"/>
        <path d="M8.2 6.5c.5-.4 1.2-.3 1.5.2l1.1 1.8c.3.5.2 1.1-.3 1.4l-.8.5c.6 1.5 1.7 2.7 3.2 3.4l.5-.8c.3-.5.9-.6 1.4-.3l1.8 1.1c.5.3.6 1 .2 1.5l-.9 1c-.6.6-1.5.8-2.3.5-3-1.2-5.3-3.6-6.4-6.6-.3-.8-.1-1.7.5-2.3z" fill="#fff"/>
        <path d="M13.5 7.2a3.4 3.4 0 0 1 3.1 3.1M13.6 5.2a5.3 5.3 0 0 1 5 5" stroke="#fff" stroke-width="1" fill="none" stroke-linecap="round"/>
      </svg>
      <span>044-987 650 312</span>
    </li>
    <li class="contact__item">
      <svg class="contact__icon" viewBox="0 0 24 24" aria-hidden="true">
        <circle cx="12" cy="12" r="12" fill="var(--forest)"/>
        <rect x="6" y="8" width="12" height="8.5" rx="1" fill="#fff"/>
        <path d="M6.3 8.4 12 13l5.7-4.6M6.3 16.2l4.2-3.8M17.7 16.2l-4.2-3.8" stroke="var(--forest)" stroke-width="0.9" fill="none"/>
      </svg>
      <span>hello@pavrel.com</span>
    </li>
  </ul>
  <p class="website">www.pavrel.com</p>
  <div class="front-band"></div>
</section>

<section class="card card--back" aria-label="Business card back">
  <p class="back-brand">PAVREL</p>
</section>

</body>
</html>
```